I need a business card for my original fine art pieces

I would like a business card design including a logo design for a new business in the art world. I am based in the Hunter Valley NSW Australia. I am a contemporary figurative, encaustic and wildlife artist. I would like to be able to upload my email and mobile number to this as well. This design should be one that I can incorporate into banners and flyers etc. Id like to incorporate one of my own images or partial image into the background or somewhere below. My initials are RJ and I would like these used as a logo type. I would like the use of some colour and it to be bright and catchy. The final design should communicate artwork custom made and commissions available.

Overview: Original Fine Artworks for sale, online, art galleries etc, Custom made to order and by commission.

Target market is world wide audience and corporate world

My figurative work is painted using acrylics in a lot of natural ochre colours that reflect the Australian Outback, on canvas, linen, paper or board: My encaustic work is created in a contemporary abstract style using a blow torch and a made with a medium of 100% pure bees wax, Damar resin, mixed media and coloured pigments, applied to Birch board. My wildlife are created using coloured pencil and mixed media on a variety of paper types or board.

```html
<!DOCTYPE html>
<html lang="en">
<head>
<meta charset="utf-8">
<title>RJ Studio Business Card</title>
<link rel="stylesheet" href="https://fonts.googleapis.com/css2?family=Cinzel:wght@400&family=Open+Sans:wght@400;600;700&display=swap">
<style>
  :root {
    --page-bg: #ecebe9;
    --card-dark: #343434;
    --accent-orange: #ff4600;
    --white: #ffffff;
    --text-light: #f2f2f2;
  }
  * { margin: 0; padding: 0; box-sizing: border-box; }
  html, body { width: 1200px; height: 900px; overflow: hidden; }
  body {
    position: relative;
    background: var(--page-bg);
    font-family: "Open Sans", Arial, sans-serif;
  }
  .card {
    position: absolute;
    background: var(--card-dark);
    overflow: hidden;
    box-shadow: 0 6px 18px rgba(0,0,0,0.25);
  }
  .card--front { left: 238px; top: 62px; width: 555px; height: 342px; }
  .card--back  { left: 459px; top: 519px; width: 559px; height: 342px; }

  .front-graphic { position: absolute; inset: 0; }

  .holder { position: absolute; left: 32px; top: 27px; color: var(--white); }
  .holder__name { font-size: 17.5px; font-weight: 700; line-height: 1.2; }
  .holder__role { font-size: 14.5px; font-weight: 400; line-height: 1.3; }

  .contact { position: absolute; left: 32px; top: 250px; list-style: none; color: var(--text-light); }
  .contact__item { display: flex; align-items: center; gap: 8px; font-size: 14.5px; height: 20.5px; }
  .contact__icon { width: 11px; height: 11px; fill: var(--text-light); flex: none; }

  .studio-name {
    position: absolute; left: 262px; top: 135px; width: 290px;
    text-align: center;
    font-family: "Open Sans", Arial, sans-serif; font-weight: 600;
    font-size: 52px; line-height: 80px; color: var(--white);
    white-space: nowrap;
  }

  .brand { position: absolute; left: 0; right: 0; top: 88px; text-align: center; }
  .brand__circle {
    width: 110px; height: 110px; margin: 0 auto;
    border: 2px solid var(--accent-orange); border-radius: 50%;
  }
  .brand__name {
    margin-top: 7px;
    font-family: "Cinzel", Georgia, serif; font-weight: 400;
    font-size: 34px; line-height: 40px; letter-spacing: 1px;
    color: var(--accent-orange);
  }
  .brand__tagline {
    font-size: 15px; letter-spacing: 3.2px; color: var(--text-light);
  }
</style>
</head>
<body>
  <section class="card card--front">
    <svg class="front-graphic" width="555" height="342" viewBox="0 0 555 342" aria-hidden="true">
      <rect x="0" y="98" width="400" height="146" fill="var(--white)"/>
      <circle cx="416" cy="170" r="175" fill="var(--white)"/>
      <rect x="0" y="106" width="400" height="130" fill="var(--accent-orange)"/>
      <circle cx="416" cy="170" r="166" fill="var(--accent-orange)"/>
    </svg>

    <div class="holder">
      <p class="holder__name">Daniel Brooks</p>
      <p class="holder__role">Managing Director</p>
    </div>

    <p class="studio-name">RJ Studio</p>

    <ul class="contact">
      <li class="contact__item">
        <svg class="contact__icon" viewBox="0 0 24 24"><path d="M6.6 10.8a15.1 15.1 0 0 0 6.6 6.6l2.2-2.2c.3-.3.7-.4 1-.2 1.1.4 2.3.6 3.6.6.6 0 1 .4 1 1V20c0 .6-.4 1-1 1C10.6 21 3 13.4 3 4c0-.6.4-1 1-1h3.5c.6 0 1 .4 1 1 0 1.3.2 2.5.6 3.6.1.3 0 .7-.2 1z"/></svg>
        044-987 654 321
      </li>
      <li class="contact__item">
        <svg class="contact__icon" viewBox="0 0 24 24"><path d="M2 5h20v14H2z"/><path d="M3 6l9 7 9-7" stroke="var(--card-dark)" stroke-width="2" fill="none"/></svg>
        hello@rjstudio.com
      </li>
      <li class="contact__item">
        <svg class="contact__icon" viewBox="0 0 24 24"><circle cx="12" cy="12" r="10"/><path d="M2 12h20M12 2c3 3 3 17 0 20M12 2c-3 3-3 17 0 20" stroke="var(--card-dark)" stroke-width="1.6" fill="none"/></svg>
        www.rjstudioart.com
      </li>
    </ul>
  </section>

  <section class="card card--back">
    <div class="brand">
      <div class="brand__circle" aria-hidden="true"></div>
      <h1 class="brand__name">Rosa Jarvis</h1>
      <p class="brand__tagline">ORIGINAL FINE ARTWORKS</p>
    </div>
  </section>
</body>
</html>
```